Redesign of business card for Cedar Ridge Mechanical

We are looking for a new design for our business cards for Cedar Ridge Mechanical. We are a plumbing & HVAC construction company, operating on the West Coast of Canada and USA. Logo attached.
Industry/Entity Type
Construction - Plumbing & HVAC
Contact Information for Business Card
Name, address, phone numbers, email, website address
Look and feel
Each slider illustrates characteristics of the customer's brand and the style your logo design should communicate.

```html
<!DOCTYPE html>
<html lang="en">
<head>
<meta charset="utf-8">
<title>Cedar Ridge Mechanical – Business Card</title>
<link rel="stylesheet" href="https://fonts.googleapis.com/css2?family=Montserrat:wght@400;700&display=swap">
<style>
  :root {
    --backdrop: #d6d6d6;
    --card: #ffffff;
    --ink: #000000;
    --paper-text: #ffffff;
    --shadow: rgba(0, 0, 0, 0.28);
  }
  * { margin: 0; padding: 0; box-sizing: border-box; }
  html, body { width: 1200px; height: 896px; overflow: hidden; }
  body {
    background: var(--backdrop);
    font-family: "Montserrat", sans-serif;
    color: var(--ink);
    position: relative;
  }
  .card {
    position: absolute;
    left: 334px;
    width: 528px;
    height: 300px;
    background: var(--card);
    border-radius: 24px;
    overflow: hidden;
    box-shadow: 0 14px 24px var(--shadow);
  }
  .card--front { top: 126px; }
  .card--back { top: 475px; }

  .brand {
    position: absolute;
    display: flex;
    align-items: center;
    gap: 14px;
    font-weight: 700;
    color: var(--ink);
    text-transform: uppercase;
  }
  .card--front .brand {
    left: 0; right: 0; top: 0; bottom: 0;
    justify-content: center;
  }
  .brand__square {
    width: 46px; height: 46px;
    background: var(--ink);
    flex: none;
  }
  .brand__name {
    font-size: 26px;
    line-height: 1.1;
    letter-spacing: 0.5px;
  }

  /* Back */
  .lower-band {
    position: absolute;
    left: 0; right: 0; top: 140px; bottom: 0;
    background: var(--ink);
  }
  .person {
    position: absolute;
    left: 0; top: 28px;
    padding-left: 20px;
    border-left: 10px solid var(--ink);
    height: 37px;
  }
  .person__name {
    font-weight: 700;
    font-size: 20px;
    line-height: 1;
    letter-spacing: 0.3px;
    margin-top: -2px;
  }
  .person__role {
    font-size: 14px;
    margin-top: 5px;
  }
  .card--back .brand {
    right: 22px; top: 46px;
    gap: 10px;
    text-align: right;
  }
  .card--back .brand__square { width: 34px; height: 34px; }
  .card--back .brand__name { font-size: 19px; }

  .contact {
    position: absolute;
    left: 20px; top: 156px;
    color: var(--paper-text);
    font-size: 14px;
    line-height: 20px;
    list-style: none;
  }
  .contact__address { margin-bottom: 10px; }
  .contact__item { display: flex; align-items: center; gap: 5px; }
  .contact__icon { width: 12px; height: 12px; fill: var(--paper-text); flex: none; }
</style>
</head>
<body>

<section class="card card--front" aria-label="Card front">
  <div class="brand">
    <span class="brand__square"></span>
    <span class="brand__name">Cedar Ridge<br>Mechanical</span>
  </div>
</section>

<section class="card card--back" aria-label="Card back">
  <div class="lower-band" role="img" aria-label="Decorative wave band"></div>

  <div class="person">
    <p class="person__name">DANIEL REYES</p>
    <p class="person__role">Managing Director</p>
  </div>

  <div class="brand">
    <span class="brand__name">Cedar Ridge<br>Mechanical</span>
    <span class="brand__square"></span>
  </div>

  <ul class="contact">
    <li class="contact__address">Your address, City<br>State, Zip 1234</li>
    <li class="contact__item">
      <svg class="contact__icon" viewBox="0 0 24 24"><path d="M6.6 10.8a15 15 0 0 0 6.6 6.6l2.2-2.2a1 1 0 0 1 1-.25 11.4 11.4 0 0 0 3.6.57 1 1 0 0 1 1 1V20a1 1 0 0 1-1 1A17 17 0 0 1 3 4a1 1 0 0 1 1-1h3.5a1 1 0 0 1 1 1c0 1.25.2 2.45.57 3.57a1 1 0 0 1-.25 1z"/></svg>
      123 456 789
    </li>
    <li class="contact__item">
      <svg class="contact__icon" viewBox="0 0 24 24"><path d="M7 1h10a2 2 0 0 1 2 2v18a2 2 0 0 1-2 2H7a2 2 0 0 1-2-2V3a2 2 0 0 1 2-2zm0 3v14h10V4zm5 15.5a1.2 1.2 0 1 0 0 2.4 1.2 1.2 0 0 0 0-2.4z"/></svg>
      123 456 789
    </li>
    <li class="contact__item">
      <svg class="contact__icon" viewBox="0 0 24 24"><path d="M2 5h20v14H2zm2 2v.5l8 5.5 8-5.5V7zm0 3v7h16v-7l-8 5.5z"/></svg>
      info@yourgmail.com
    </li>
    <li class="contact__item">
      <svg class="contact__icon" viewBox="0 0 24 24"><path d="M12 2a10 10 0 1 0 0 20 10 10 0 0 0 0-20zm0 2a8 8 0 0 1 7.9 7H4.1A8 8 0 0 1 12 4zm-7.9 9h15.8A8 8 0 0 1 4.1 13z"/></svg>
      www.yourwebsite.com
    </li>
  </ul>
</section>

</body>
</html>
```